Oil Field Service company needs professional business cards

Looking to clean up our current company business cards and look a little more professional. Brenwick Casing Services is a US based company that services the oil field. We deal with engineers, managers and oil rigs....................................................................................................................................................................................................................................................................................................................................................................................................

Target Market(s)

Oil and Gas professionals

Industry/Entity Type

Oil And Gas

Contact Information for Business Card

See attached photo as example

Font styles to use
Sans Serif

Colors
ec1f27

Requirements
Must have
• Company Logo, Name, Title, Cell, Office, Fax, Email.
• See attached photo
Nice to have
• External CRT, Internal CRT, Casing Crews, Torque Turn, Laydown Machine
Should not have
• Do not introduce any new pictures and keep it professional looking

```html
<!DOCTYPE html>
<html lang="en">
<head>
<meta charset="utf-8">
<title>Brenwick Casing Services – Business Card</title>
<link href="https://fonts.googleapis.com/css2?family=Roboto:wght@400;500;700&display=swap" rel="stylesheet">
<style>
  :root {
    --brand-red: #d0201f;
    --brand-red-dark: #bf1c1c;
    --slate: #3e5566;
    --card-white: #f6f6f5;
    --ink: #3a3f45;
    --backdrop: #e4e4e2;
  }
  * { box-sizing: border-box; margin: 0; padding: 0; }
  html, body {
    width: 1200px; height: 576px; overflow: hidden;
    background: var(--backdrop);
    font-family: "Roboto", Arial, sans-serif;
  }
  .stage { position: relative; width: 1200px; height: 576px; }
  .card {
    position: absolute; top: 140px;
    width: 484px; height: 294px;
    border-radius: 7px; overflow: hidden;
    box-shadow: 0 2px 5px rgba(0,0,0,0.22);
  }
  .card-front {
    left: 80px;
    background: linear-gradient(180deg, var(--brand-red) 0%, var(--brand-red-dark) 100%);
    display: flex; flex-direction: column; align-items: center; justify-content: center;
    color: #fff;
  }
  .card-back { left: 636px; background: var(--card-white); }
  .wordmark { font-weight: 700; text-align: center; line-height: 1; }
  .wordmark-name { display: block; font-size: 46px; letter-spacing: 1px; }
  .wordmark-tag { display: block; font-size: 15px; letter-spacing: 3px; margin-top: 10px; }
  .card-front .wordmark { margin-bottom: 18px; }
  .header-band {
    position: absolute; left: 0; top: 0;
    width: 100%; height: 96px;
    background: var(--brand-red);
  }
  .header-rule {
    position: absolute; left: 0; top: 100px;
    width: 100%; height: 4px;
    background: var(--slate);
  }
  .service-list {
    position: absolute; top: 14px; right: 26px;
    list-style: none; text-align: right;
    color: #fff; font-weight: 500; font-size: 13px; line-height: 18px;
  }
  .service-list li::after { content: " «"; padding-left: 4px; }
  .card-back .wordmark {
    position: absolute; left: 28px; top: 124px;
    color: var(--slate); text-align: left;
  }
  .card-back .wordmark-name { font-size: 40px; }
  .card-back .wordmark-tag { font-size: 13px; letter-spacing: 2.6px; margin-top: 8px; padding-left: 26px; }
  .contact {
    position: absolute; top: 222px; list-style: none;
    font-size: 12px; line-height: 16px; color: var(--ink);
  }
  .contact li { display: flex; align-items: center; gap: 8px; }
  .contact svg { width: 10px; height: 10px; fill: var(--brand-red); flex: none; }
  .contact-phones { left: 28px; }
  .contact-details { left: 250px; }
</style>
</head>
<body>
<main class="stage">
  <section class="card card-front" aria-label="Card front">
    <div class="wordmark">
      <span class="wordmark-name">BRENWICK</span>
      <span class="wordmark-tag">CASING SERVICES</span>
    </div>
  </section>

  <section class="card card-back" aria-label="Card back">
    <div class="header-band" role="img" aria-label="Red header band with decorative wave"></div>
    <div class="header-rule" aria-hidden="true"></div>

    <ul class="service-list">
      <li>Laydown Machine</li>
      <li>Casing Crew</li>
      <li>Torque Turn</li>
      <li>Mud Tool</li>
    </ul>

    <div class="wordmark">
      <span class="wordmark-name">BRENWICK</span>
      <span class="wordmark-tag">CASING SERVICES</span>
    </div>

    <ul class="contact contact-phones">
      <li><svg viewBox="0 0 10 10"><path d="M2,0.5 L3.6,2.6 L2.8,3.6 C3.4,5 4.8,6.4 6.3,7.1 L7.3,6.3 L9.5,7.9 L8.4,9.6 C4.3,9.4 0.6,5.6 0.4,1.6 Z"/></svg>(580) 555-0142</li>
      <li><svg viewBox="0 0 10 10"><path d="M0.5,3.5 C2,1.5 8,1.5 9.5,3.5 L8.5,4.6 L7,3.8 V3 H3 V3.8 L1.5,4.6 Z M2,5 H8 L9,9 H1 Z"/></svg>(580) 555-0178</li>
      <li><svg viewBox="0 0 10 10"><path d="M2.5,0.5 H7.5 V3 H2.5 Z M0.5,3.5 H9.5 V7.5 H8 V6 H2 V7.5 H0.5 Z M2.5,6.5 H7.5 V9.5 H2.5 Z"/></svg>(580) 555-0193</li>
    </ul>

    <ul class="contact contact-details">
      <li><svg viewBox="0 0 10 10"><path d="M5,0.3 C2.9,0.3 1.5,1.9 1.5,3.8 C1.5,6.3 5,9.7 5,9.7 C5,9.7 8.5,6.3 8.5,3.8 C8.5,1.9 7.1,0.3 5,0.3 Z M5,2.5 A1.3,1.3 0 1 1 5,5.1 A1.3,1.3 0 1 1 5,2.5 Z"/></svg>Harlow Ridge, OK 73099</li>
      <li><svg viewBox="0 0 10 10"><path d="M0.5,2 H9.5 V8 H0.5 Z M1,2.4 L5,5.4 L9,2.4" stroke="#fff" stroke-width="0.8"/></svg>jkessler@brenwickcasing.com</li>
      <li><svg viewBox="0 0 10 10"><circle cx="5" cy="5" r="4.5"/><path d="M0.5,5 H9.5 M5,0.5 C2.8,3 2.8,7 5,9.5 M5,0.5 C7.2,3 7.2,7 5,9.5" stroke="#fff" stroke-width="0.7" fill="none"/></svg>www.brenwickcasing.com</li>
    </ul>
  </section>
</main>
</body>
</html>
```